Norvane Website Design (New Start Up Investment Management Firm)

We need a website designed. We have attached a Powerpoint with our proposed website content (which is quite minimal), the format is just a suggestion but we would like to see your alternative and improved ideas. We are a boutique investment firm so are looking for something sleek and professional. I have included on the last page of the attachment our brand colours and font styles as well as attaching our logo design. We would like the successful designer to design the website and build the buttons etc.

On the "Contact Us" page, we are open to suggestions on how best to show the map, whether is should be static or open a google maps page. We would like the phone number and email address to be set up so people can click on them on their phone and it calls us or emails us directly.

We would prefer not to have photos of landscapes on the site.
Our website is hosted on a Linux based website.

We would also like 3 links at the bottom of each page for links to pdfs:
- Disclaimer, Terms and Conditions of Web Site Use
- Stewardship
- Pillar III

Target Market(s)

Institutional Investors

Industry/Entity Type

Investment

Coding

Coded - Design and coding required

Number of Pages Required

3 page

Font styles to use
Other font styles liked:
• Logo: Lato, Text: Source Sans Pro

Colors

Designer to choose colors to be used in the design.

Requirements
Must have
• The website must use the colours and fonts on the last page of the attached powerpoint. I can't see an option to select the exact colour palette below so please look at the PPT.
• For others please see Project description.
Should not have
• Landscape photos

```html
<!DOCTYPE html>
<html lang="en">
<head>
<meta charset="utf-8">
<title>Norvane Investment Management</title>
<link href="https://fonts.googleapis.com/css2?family=Lato:wght@400;700&family=Source+Sans+3:wght@400&display=swap" rel="stylesheet">
<style>
  :root {
    --navy: #0b2f66;
    --navy-deep: #02275a;
    --white: #ffffff;
    --hero-light: #9dbde0;
    --hero-mid: #6f98c8;
    --hero-dark: #3a679f;
    --btn-active-top: #72b6e8;
    --btn-active-bottom: #3c8cd4;
    --btn-top: #0b3b78;
    --btn-bottom: #01204f;
    --ring: #d9d9d9;
    --icon-grey: #b5b5b5;
  }
  * { margin: 0; padding: 0; box-sizing: border-box; }
  html, body { width: 1200px; height: 651px; overflow: hidden; background: var(--white); }
  body { position: relative; font-family: "Lato", sans-serif; }

  .site-header { position: absolute; left: 0; top: 0; width: 1200px; height: 94px; background: var(--white); }
  .brand { position: absolute; left: 86px; top: 26px; display: flex; align-items: center; gap: 10px; }
  .brand-mark { width: 40px; height: 40px; background: var(--navy); }
  .brand-name { font-family: "Lato", sans-serif; font-weight: 700; font-size: 40px; line-height: 1; color: var(--navy); letter-spacing: 1px; }

  .menu-toggle { position: absolute; left: 1057px; top: 19px; width: 57px; height: 57px; border: 1px solid var(--ring); border-radius: 50%; }
  .menu-toggle svg { position: absolute; left: 20px; top: 21px; }

  .hero { position: absolute; left: 0; top: 94px; width: 1200px; height: 495px; }
  .hero-backdrop { position: absolute; inset: 0; background: linear-gradient(100deg, var(--hero-light) 0%, var(--hero-mid) 50%, var(--hero-dark) 100%); }

  .section-nav { position: absolute; left: 86px; top: 191px; width: 249px; list-style: none; }
  .section-nav li { height: 47px; margin-bottom: 8px; border-radius: 3px; background: linear-gradient(var(--btn-top), var(--btn-bottom)); color: var(--white); font-weight: 700; font-size: 14.5px; line-height: 47px; padding-left: 21px; white-space: nowrap; overflow: hidden; }
  .section-nav li.is-active { background: linear-gradient(var(--btn-active-top), var(--btn-active-bottom)); }

  .intro { position: absolute; left: 383px; top: 186px; width: 720px; color: var(--white); white-space: nowrap; }
  .intro-lead { font-family: "Lato", sans-serif; font-weight: 700; font-size: 12.9px; line-height: 27.4px; text-transform: uppercase; }
  .intro-body { margin-top: 21px; font-family: Arial, "Source Sans 3", sans-serif; font-size: 12.4px; line-height: 27.4px; }

  .site-footer { position: absolute; left: 0; top: 589px; width: 1200px; height: 62px; background: var(--navy-deep); color: var(--white); font-size: 12.3px; text-align: center; line-height: 62px; white-space: nowrap; }
  .site-footer a { color: var(--white); text-decoration: underline; }
  .site-footer .sep { margin: 0 9px; }
</style>
</head>
<body>
  <header class="site-header">
    <div class="brand"><span class="brand-mark"></span><span class="brand-name">NORVANE</span></div>
    <div class="menu-toggle">
      <svg width="17" height="14" viewBox="0 0 17 14"><rect y="0" width="17" height="3" fill="var(--icon-grey)"/><rect y="5.5" width="17" height="3" fill="var(--icon-grey)"/><rect y="11" width="17" height="3" fill="var(--icon-grey)"/></svg>
    </div>
  </header>

  <section class="hero">
    <div class="hero-backdrop" role="img" aria-label="Blue-toned photo of hands reviewing financial charts beside a laptop with data graphics"></div>
    <ul class="section-nav">
      <li class="is-active">ABOUT NORVANE</li>
      <li>OUR APPROACH &amp; PHILOSOPHY</li>
      <li>CONTACT US</li>
    </ul>
    <div class="intro">
      <p class="intro-lead">Norvane Investment Management was founded in 2016 with a clear vision to create an independent<br>&amp; nimble firm focused on generating superior risk-adjusted returns.</p>
      <p class="intro-body">Norvane has designed an innovative investment approach which aims to harness the best elements of alternative investment<br>management whilst reducing its recognised shortcomings. We are a performance and client focused firm, committed to building<br>lasting relationships, treating our clients like partners rather than revenue streams.</p>
    </div>
  </section>

  <footer class="site-footer">
    © Copy Right 2017 Norvane IM.All Rights Reserved.<a href="#">Disclaimer, Terms and Conditions</a><span class="sep">|</span><a href="#">Stewardship</a><span class="sep">|</span><a href="#">Pillar III</a>
  </footer>
</body>
</html>
```